Redesign of business card for Cedar Ridge Mechanical

We are looking for a new design for our business cards for Cedar Ridge Mechanical. We are a plumbing & HVAC construction company, operating on the West Coast of Canada and USA. Logo attached.
Industry/Entity Type
Construction - Plumbing & HVAC
Contact Information for Business Card
Name, address, phone numbers, email, website address
Look and feel
Each slider illustrates characteristics of the customer's brand and the style your logo design should communicate.

```html
<!DOCTYPE html>
<html lang="en">
<head>
<meta charset="utf-8">
<title>Cedar Ridge Mechanical – Business Card</title>
<link href="https://fonts.googleapis.com/css2?family=Montserrat:wght@400;500;700&display=swap" rel="stylesheet">
<style>
  :root {
    --stage: #7d6a52;
    --card-front: #ffffff;
    --card-back: #1c1c1c;
    --ink: #1a1a1a;
    --ink-soft: #222222;
    --back-mark: #0d0d0d;
    --back-edge: #3a3a3a;
  }
  html, body {
    margin: 0;
    padding: 0;
    width: 900px;
    height: 1200px;
    overflow: hidden;
    background: var(--stage);
    font-family: "Montserrat", Arial, sans-serif;
  }
  .canvas {
    position: relative;
    width: 900px;
    height: 1200px;
  }
  .card {
    position: absolute;
    left: 80px;
    width: 742px;
    height: 440px;
    border-radius: 22px;
    box-shadow: 0 10px 24px rgba(0,0,0,0.35);
    overflow: hidden;
  }
  .card--front { top: 131px; background: var(--card-front); color: var(--ink); }
  .card--back { top: 638px; background: var(--card-back); }

  .holder-name {
    position: absolute; left: 37px; top: 46px; margin: 0;
    font-size: 26px; font-weight: 700; letter-spacing: 0.2px;
  }
  .holder-title {
    position: absolute; left: 37px; top: 80px; margin: 0;
    font-size: 16px; font-weight: 500;
  }
  .address {
    position: absolute; left: 40px; top: 258px; margin: 0;
    font-size: 16px; line-height: 20px; font-style: normal; font-weight: 500;
  }
  .contact-list {
    position: absolute; left: 38px; top: 327px; margin: 0; padding: 0;
    list-style: none; font-size: 16px; font-weight: 500;
  }
  .contact-list li {
    display: flex; align-items: center; height: 31px;
  }
  .contact-list svg { width: 16px; height: 16px; margin-right: 11px; fill: var(--ink-soft); }

  .brand {
    position: absolute; display: flex; align-items: center; gap: 16px;
  }
  .brand__square { flex: none; width: 34px; height: 34px; }
  .brand__name {
    margin: 0; font-weight: 700; text-transform: uppercase;
    line-height: 1.1; letter-spacing: 1px;
  }
  .card--front .brand { left: 308px; top: 150px; }
  .card--front .brand__square { background: var(--ink); }
  .card--front .brand__name { font-size: 30px; color: var(--ink); }

  .card--back .brand { left: 180px; top: 160px; }
  .card--back .brand__square { background: var(--back-mark); width: 44px; height: 44px; }
  .card--back .brand__name { font-size: 36px; color: var(--back-mark); }
</style>
</head>
<body>
<main class="canvas">
  <section class="card card--front">
    <h1 class="holder-name">Daniel Brooks</h1>
    <p class="holder-title">Managing Director</p>

    <div class="brand">
      <span class="brand__square"></span>
      <p class="brand__name">Cedar Ridge<br>Mechanical</p>
    </div>

    <address class="address">214 Fir Hollow Road<br>Bellingham, WA 98225</address>

    <ul class="contact-list">
      <li>
        <svg viewBox="0 0 24 24" aria-hidden="true"><path d="M6.6 10.8c1.4 2.8 3.8 5.1 6.6 6.6l2.2-2.2c.3-.3.7-.4 1-.2 1.1.4 2.3.6 3.6.6.6 0 1 .4 1 1V20c0 .6-.4 1-1 1C10.6 21 3 13.4 3 4c0-.6.4-1 1-1h3.5c.6 0 1 .4 1 1 0 1.3.2 2.5.6 3.6.1.3 0 .7-.2 1L6.6 10.8z"/></svg>
        <span>888.555.0142</span>
      </li>
      <li>
        <svg viewBox="0 0 24 24" aria-hidden="true"><path d="M2 5h20v2l-10 6L2 7V5zm0 4l10 6 10-6v10H2V9z"/></svg>
        <span>info@cedarridgemech.com</span>
      </li>
      <li>
        <svg viewBox="0 0 24 24" aria-hidden="true"><path d="M12 2a10 10 0 1 0 0 20 10 10 0 0 0 0-20zm6.9 6h-3a15 15 0 0 0-1.3-4A8 8 0 0 1 18.9 8zM12 4c.8 1.2 1.5 2.5 1.9 4h-3.8c.4-1.5 1.1-2.8 1.9-4zM4.3 14a8 8 0 0 1 0-4h3.4a16 16 0 0 0 0 4H4.3zm.8 2h3a15 15 0 0 0 1.3 4A8 8 0 0 1 5.1 16zM8.1 8h-3a8 8 0 0 1 4.3-4c-.6 1.2-1 2.6-1.3 4zM12 20c-.8-1.2-1.5-2.5-1.9-4h3.8c-.4 1.5-1.1 2.8-1.9 4zm2.3-6H9.7a14 14 0 0 1 0-4h4.6a14 14 0 0 1 0 4zm.3 6a15 15 0 0 0 1.3-4h3a8 8 0 0 1-4.3 4zm1.7-6a16 16 0 0 0 0-4h3.4a8 8 0 0 1 0 4h-3.4z"/></svg>
        <span>www.cedarridgemech.com</span>
      </li>
    </ul>
  </section>

  <section class="card card--back">
    <div class="brand">
      <span class="brand__square"></span>
      <p class="brand__name">Cedar Ridge<br>Mechanical</p>
    </div>
  </section>
</main>
</body>
</html>
```